ultra-minimalist business card

front (black background, matte):

reza t. kovin
writer | photographer
get@rezakovin.com

back (white background, matte):

a picture speaks a thousand words;
a word draws a thousand pictures.

www.rezakovin.com

all text should be small (white or silver - as long as it shows against the black - on the front; black or gray - as long as it shows against the white - on the back).

feel free to get creative in terms of arrangement, alignment, and font type, but remember, the overall style is minimalist, so nothing too fancy, please.

thanks.

```html
<!DOCTYPE html>
<html lang="en">
<head>
<meta charset="utf-8">
<title>Reza T. Kovin — Business Card</title>
<link href="https://fonts.googleapis.com/css2?family=Questrial&display=swap" rel="stylesheet">
<style>
  :root {
    --stage: #ececec;
    --card-light: #f7f7f7;
    --card-light-shade: #e6e6e6;
    --card-dark: #2b2b2b;
    --card-dark-shade: #232323;
    --ink-dark: #1a1a1a;
    --ink-light: #f2f2f2;
    --rule-dark: #111111;
    --rule-light: #f5f5f5;
  }
  * { margin: 0; padding: 0; box-sizing: border-box; }
  html, body {
    width: 1200px;
    height: 586px;
    overflow: hidden;
    background: var(--stage);
  }
  .stage {
    position: relative;
    width: 1200px;
    height: 586px;
    font-family: "Questrial", "Century Gothic", sans-serif;
  }
  .card {
    position: absolute;
    top: 143px;
    width: 502px;
    height: 301px;
    overflow: hidden;
  }
  .card--back { left: 61px; }
  .card--front { left: 619px; }

  .card__texture {
    position: absolute;
    inset: 0;
  }
  .card--back .card__texture {
    background: linear-gradient(135deg, var(--card-light) 0%, #ffffff 35%, var(--card-light-shade) 60%, #ffffff 100%);
  }
  .card--front .card__texture {
    background: linear-gradient(135deg, var(--card-dark-shade) 0%, var(--card-dark) 40%, var(--card-dark-shade) 70%, var(--card-dark) 100%);
  }

  .card__rule {
    position: absolute;
    width: 1.5px;
  }
  .card--back .card__rule { left: 30px; background: var(--rule-dark); }
  .card--front .card__rule { left: 471px; background: var(--rule-light); }
  .card__rule--upper { top: 0; height: 258px; }
  .card__rule--lower { top: 282px; bottom: 0; }

  .tagline {
    position: absolute;
    left: 47px;
    top: 216px;
    color: var(--ink-dark);
    font-size: 13.5px;
    line-height: 23px;
  }
  .website {
    position: absolute;
    left: 30px;
    top: 263px;
    color: var(--ink-dark);
    font-size: 12.5px;
    font-weight: 700;
    letter-spacing: 7.4px;
  }

  .identity {
    position: absolute;
    right: 41px;
    top: 210px;
    text-align: right;
    color: var(--ink-light);
  }
  .identity__name {
    font-size: 19px;
    line-height: 24px;
  }
  .identity__role {
    font-size: 13.5px;
    font-style: italic;
    line-height: 22px;
  }
  .identity__email {
    position: absolute;
    right: 29px;
    top: 263px;
    color: var(--ink-light);
    font-size: 13.5px;
    letter-spacing: 1px;
  }
</style>
</head>
<body>
  <main class="stage">
    <section class="card card--back" aria-label="Card back">
      <div class="card__texture" role="img" aria-label="Faceted low-poly texture in soft whites and light greys"></div>
      <div class="card__rule card__rule--upper"></div>
      <div class="card__rule card__rule--lower"></div>
      <p class="tagline">A Picture Speaks A Thousand Words<br>A Word Draws A Thousand Pictures</p>
      <p class="website">www.rezakovin.com</p>
    </section>

    <section class="card card--front" aria-label="Card front">
      <div class="card__texture" role="img" aria-label="Faceted low-poly texture in deep charcoal tones"></div>
      <div class="card__rule card__rule--upper"></div>
      <div class="card__rule card__rule--lower"></div>
      <div class="identity">
        <p class="identity__name">Reza T. Kovin</p>
        <p class="identity__role">Writer | Photographer</p>
      </div>
      <p class="identity__email">get@rezakovin.com</p>
    </section>
  </main>
</body>
</html>
```